General Surgeon flyer to be distributed to GPs

I am a general surgeon and I would like to have a flyer designed aiming to introduce myself to GPs.

Name: Dr Tobias Lindqvar MD, FRACS
Address: Suite 4C, Brellam private hospital, 418 Corvell Parade, Halloway, VIC, 3188
T: (03) 9587 6102
F: (03) 9463 1178
E: referrals@quillfordsurgeons.com.au
Website: www.quillfordsurgeons.com.au

Tobias is a highly trained general surgeon, having completed extensive surgical training at Tarrowby health, Pellington and Corrigan Health networks. He further specialized by completing a fellowship in Oesophagogastric and Bariatric Surgery at St Aldric’s Hospital Melbourne, one of Victoria’s leading Upper GI surgical centres.

With expertise in both advanced laparoscopic and open surgical techniques, he performs a wide range of procedures involving the gastrointestinal system, abdominal wall hernias, as well as other major and minor general surgical operations. In addition to holding appointments at Tarrowby Health, he also operates at Brellam and Fernwick Private Hospitals.

Dr Lindqvar is committed to providing patient-centred care with a focus on surgical precision, safety, and long-term health outcomes.

He is also fluent in Farsi/Pesrian.
Outside of surgery, Tobias enjoys playings classical piano and spending time with his 6-year-old Bordoodle on long walks.

Upper GI & Bariatric Surgery:
Hiatus hernia repair, sleeve gastrectomy, gastric bypass
General Surgery conditions:
Gallbladder Surgery: Laparoscopic cholecystectomy
Hernia Repair: Laparoscopic and open surgery (inguinal,
umbilical, incisional)
Anorectal Procedures: Haemorrhoidectomy, haemorrhoid banding
Hand Surgery: Carpal tunnel release, Lymph Node Biopsy
Ingrown Toenail Surgery
Skin & Soft Tissue Surgery: Skin cancer removal, lipoma and
sebaceous cyst excision
Emergency Surgery: Laparotomy, Appendicectomy, bowel resection
Endoscopy: Diagnostic and therapeutic procedures

```html
<!DOCTYPE html>
<html lang="en">
<head>
<meta charset="utf-8">
<title>Dr Tobias Lindqvar – General Surgeon</title>
<link rel="stylesheet" href="https://fonts.googleapis.com/css2?family=Montserrat:wght@400;500;600;700;800&display=swap">
<style>
  :root {
    --page-bg: #eef0f2;
    --paper: #ffffff;
    --navy-deep: #0c3058;
    --navy: #16457a;
    --sky: #deedfc;
    --mist: #e5e6e8;
    --mist-dark: #d4d5d7;
    --ink: #0f2d54;
    --title-blue: #6f98cf;
    --address-ink: #3a5a8a;
    --white: #ffffff;
  }
  * { box-sizing: border-box; margin: 0; padding: 0; }
  html, body {
    width: 1113px; height: 1200px; overflow: hidden;
    background: var(--page-bg);
    font-family: "Montserrat", sans-serif;
    color: var(--ink);
  }
  .flyer {
    position: absolute; left: 132px; top: 0;
    width: 849px; height: 1200px;
    background: var(--paper);
    display: flex; flex-direction: column;
  }
  .site-url {
    height: 122px;
    display: flex; align-items: flex-end; justify-content: center;
    padding-bottom: 20px;
    font-size: 18px; letter-spacing: 3.2px; color: var(--ink);
  }
  .name-band {
    height: 60px; background: var(--navy-deep);
    display: flex; align-items: center; justify-content: center;
    color: var(--title-blue); font-size: 24px; letter-spacing: 0.3px;
  }
  .name-band strong { font-weight: 800; margin-right: 14px; }
  .name-band span { font-weight: 500; }
  .bio {
    height: 299px; background: var(--navy);
    padding: 27px 68px 0;
    color: var(--white); font-size: 15.8px; line-height: 23px; letter-spacing: 0.5px;
  }
  .bio p + p { margin-top: 18px; }
  .bio .justified { text-align: justify; }
  .services {
    height: 467px; background: var(--sky);
    padding: 33px 68px 0 73px;
  }
  .service-list { list-style: none; }
  .service-list li {
    position: relative; padding-left: 17px; margin-bottom: 13px;
  }
  .service-list li::before {
    content: ""; position: absolute; left: 0; top: 6px;
    width: 7px; height: 7px; border-radius: 50%; background: var(--ink);
  }
  .service-title {
    font-size: 15.8px; font-weight: 700; letter-spacing: 0.6px; line-height: 20px;
  }
  .service-detail {
    font-size: 16px; letter-spacing: 0.6px; line-height: 23px;
  }
  .credentials {
    height: 107px; background: var(--mist);
    display: flex; align-items: center; justify-content: center; gap: 60px;
  }
  .credential-badge {
    width: 290px; height: 52px; border-radius: 6px; background: #c9d3e0;
  }
  .practice-name {
    display: flex; align-items: center; gap: 10px;
    font-size: 16px; font-weight: 700; color: var(--navy);
  }
  .practice-name .dot {
    width: 22px; height: 22px; border-radius: 50%; background: var(--navy);
  }
  .address-bar {
    height: 31px; background: var(--mist-dark);
    display: flex; align-items: center; justify-content: center;
    font-size: 12.4px; color: var(--address-ink); letter-spacing: 0.3px;
  }
  .contact {
    flex: 1; display: flex; align-items: center; justify-content: space-between;
    padding: 0 68px 20px;
  }
  .contact-lines { font-size: 9.8px; letter-spacing: 1.5px; line-height: 13px; }
  .phone {
    display: flex; align-items: center; gap: 18px;
    font-size: 32px; font-weight: 700; letter-spacing: 0.5px;
  }
</style>
</head>
<body>
<main class="flyer">
  <header class="site-url">www.quillfordsurgeons.com.au</header>

  <h1 class="name-band"><strong>DR TOBIAS LINDQVAR</strong><span>MD, FRACS</span></h1>

  <section class="bio">
    <p class="justified">With expertise in both advanced laparoscopic and open surgical techniques, he performs a wide range of procedures involving the gastrointestinal system, abdominal wall hernias, as well as other major and minor general surgical operations. In addition to holding appointments at Tarrowby Health, he also operates at Brellam and Fernwick Private Hospitals.</p>
    <p>Dr Lindqvar is committed to providing patient-centred care with a focus on surgical precision, safety, and long-term health outcomes.</p>
    <p>He is also fluent in Farsi/Pesrian. Outside of surgery, Tobias enjoys playings classical piano and spending time with his 6-year-old Bordoodle on long walks.</p>
  </section>

  <section class="services">
    <ul class="service-list">
      <li><div class="service-title">UPPER GI &amp; BARIATRIC SURGERY</div><div class="service-detail">Upper GI &amp; Bariatric Surgery:</div></li>
      <li><div class="service-title">GENERAL SURGERY CONDITIONS</div><div class="service-detail">Gallbladder Surgery: Laparoscopic cholecystectomy</div></li>
      <li><div class="service-title">HERNIA REPAIR</div><div class="service-detail">Laparoscopic and open surgery (inguinal, umbilical, incisional)</div></li>
      <li><div class="service-title">ANORECTAL PROCEDURES</div><div class="service-detail">Haemorrhoidectomy, haemorrhoid banding</div></li>
      <li><div class="service-title">HAND SURGERY</div><div class="service-detail">Carpal tunnel release, Lymph Node Biopsy Ingrown Toenail Surgery</div></li>
      <li><div class="service-title">SKIN &amp; SOFT TISSUE SURGERY</div><div class="service-detail">Skin cancer removal, lipoma and sebaceous cyst excision</div></li>
      <li><div class="service-title">EMERGENCY SURGERY</div><div class="service-detail">Laparotomy, Appendicectomy, bowel resection Endoscopy: Diagnostic and therapeutic procedures</div></li>
    </ul>
  </section>

  <section class="credentials">
    <div class="credential-badge" role="img" aria-label="Surgical college fellowship badge"></div>
    <div class="practice-name"><span class="dot"></span>Quillford Surgeons</div>
  </section>

  <div class="address-bar">Suite 4C, Brellam private hospital, 418 Corvell Parade, Halloway, VIC, 3188</div>

  <footer class="contact">
    <div class="contact-lines">
      <div>www.quillfordsurgeons.com.au</div>
      <div>referrals@quillfordsurgeons.com.au</div>
    </div>
    <div class="phone">
      <svg width="20" height="32" viewBox="0 0 20 32" aria-hidden="true">
        <rect x="1.5" y="1.5" width="17" height="29" rx="3" fill="none" stroke="var(--ink)" stroke-width="2"/>
        <line x1="7" y1="26" x2="13" y2="26" stroke="var(--ink)" stroke-width="2" stroke-linecap="round"/>
      </svg>
      <span>(03) 9587 6102</span>
    </div>
  </footer>
</main>
</body>
</html>
```